Weightloss company needs Business Card

We want a business card that is clean and professional, yet portrays that we are a friendly, innovative, and versatile program designed to fit the needs of our clients.
I would like there to be 2 sides, one side having an appointment card, and the other side containing the logo and business information. There can be decorations on both sides. The logo is attached.

Target Market(s)

Men and women 40-60

Industry/Entity Type

Business

Contact Information for Business Card

Font styles to use
Sans Serif

Requirements
Must have
• The logo, space for business information
Nice to have
• The colors in the logo
Should not have
• No pictures of people or food

```html
<!DOCTYPE html>
<html lang="en">
<head>
<meta charset="utf-8">
<title>Renew Turn Wellness – Business Card</title>
<link rel="stylesheet" href="https://fonts.googleapis.com/css2?family=Open+Sans:ital,wght@0,400;0,600;0,700;1,400&display=swap">
<style>
  :root {
    --pink: #e8185a;
    --cyan: #35c6ea;
    --ink: #4a4a4a;
    --rule: #d9d9d9;
    --dots: #9a9a9a;
    --paper: #ffffff;
    --backdrop: #ece9e4;
  }
  * { box-sizing: border-box; margin: 0; padding: 0; }
  html, body { width: 1200px; height: 950px; overflow: hidden; }
  body {
    background: var(--backdrop);
    font-family: "Open Sans", Arial, sans-serif;
    color: var(--ink);
    position: relative;
  }
  .card {
    position: absolute;
    left: 230px;
    width: 740px;
    height: 423px;
    background: var(--paper);
    border-radius: 22px;
    overflow: hidden;
    box-shadow: 0 6px 18px rgba(0,0,0,.12);
  }
  .card--front { top: 40px; }
  .card--back { top: 487px; }

  /* Front */
  .brand {
    position: absolute; left: 50px; top: 0; width: 290px; height: 380px;
    display: flex; align-items: center; gap: 12px;
  }
  .brand__dot { width: 22px; height: 22px; border-radius: 50%; background: var(--cyan); flex: none; }
  .brand__name { color: var(--pink); font-weight: 700; font-size: 30px; line-height: 1.1; }
  .divider {
    position: absolute; left: 365px; top: 50px; width: 1px; height: 250px; background: var(--rule);
  }
  .contact { position: absolute; left: 400px; top: 60px; }
  .contact__name { color: var(--pink); font-size: 26px; font-weight: 600; letter-spacing: .5px; line-height: 1.1; }
  .contact__title { color: var(--cyan); font-size: 16px; font-weight: 600; margin-bottom: 14px; }
  .contact__line { font-size: 16px; line-height: 1.55; }
  .contact__row { display: flex; align-items: center; gap: 10px; font-size: 16px; line-height: 1.65; }
  .contact__row svg { width: 15px; height: 15px; flex: none; }
  .edge-band {
    position: absolute; left: 0; right: 0; bottom: 0; height: 18px; background: var(--cyan);
  }
  .web-tab {
    position: absolute; right: 0; bottom: 18px; width: 300px; height: 44px;
    background: var(--pink); border-top-left-radius: 22px;
    color: #fff; font-size: 17px; font-weight: 600; letter-spacing: .5px;
    display: flex; align-items: center; justify-content: center;
  }

  /* Back */
  .appt { position: absolute; inset: 36px 52px 30px; }
  .appt__title {
    color: var(--pink); font-weight: 700; font-size: 30px; text-align: center; margin-bottom: 26px;
  }
  .field { display: flex; align-items: flex-end; gap: 8px; font-size: 17px; color: var(--pink); margin-bottom: 24px; }
  .field__line { flex: 1; border-bottom: 2px dotted var(--dots); height: 18px; }
  .field__suffix { font-size: 13px; }
  .field-pair { display: flex; gap: 36px; }
  .field-pair .field { flex: 1; }
  .days { display: flex; justify-content: space-between; margin: 4px 0 30px; }
  .day { display: flex; align-items: center; gap: 7px; color: var(--pink); font-size: 17px; }
  .day__box { width: 15px; height: 15px; border: 1.5px solid var(--ink); }
  .notice { font-style: italic; font-size: 14px; text-align: center; color: var(--ink); }
</style>
</head>
<body>
  <section class="card card--front" aria-label="Card front">
    <div class="brand">
      <span class="brand__dot"></span>
      <span class="brand__name">Renew Turn Wellness</span>
    </div>
    <div class="divider"></div>
    <div class="contact">
      <p class="contact__name">DANIEL HART</p>
      <p class="contact__title">CEO/FOUNDER</p>
      <p class="contact__line">214 Birchwood Road</p>
      <p class="contact__line" style="margin-bottom:6px">Fairview, Oregon 97024</p>
      <p class="contact__row">
        <svg viewBox="0 0 16 16"><path fill="#e8185a" d="M3.5 1.5l2.5 2.8-1.4 1.8c.9 2 2.4 3.5 4.3 4.4l1.8-1.4 2.8 2.5-1.3 2.4C7.4 13.8 2.2 8.6 1.2 2.9z"/></svg>
        555 210 4471
      </p>
      <p class="contact__row">
        <svg viewBox="0 0 16 16"><rect x="4" y="1" width="8" height="14" rx="1.5" fill="none" stroke="#e8185a" stroke-width="1.6"/><circle cx="8" cy="12.5" r="1" fill="#e8185a"/></svg>
        555 318 9026
      </p>
      <p class="contact__row">
        <svg viewBox="0 0 16 16"><rect x="2" y="6" width="12" height="8" rx="1" fill="#e8185a"/><rect x="4.5" y="1.5" width="7" height="5" fill="none" stroke="#e8185a" stroke-width="1.4"/></svg>
        555 764 3185
      </p>
      <p class="contact__row">
        <svg viewBox="0 0 16 16"><rect x="1" y="3" width="14" height="10" rx="1" fill="#e8185a"/><path d="M1.5 4l6.5 5 6.5-5" fill="none" stroke="#fff" stroke-width="1.3"/></svg>
        hello@renewturn.com
      </p>
    </div>
    <div class="web-tab">www.renewturn.com</div>
    <div class="edge-band"></div>
  </section>

  <section class="card card--back" aria-label="Card back">
    <div class="appt">
      <h1 class="appt__title">Next Appointment</h1>
      <div class="field"><span>Name :</span><span class="field__line"></span></div>
      <div class="field-pair">
        <div class="field"><span>Date :</span><span class="field__line"></span></div>
        <div class="field"><span>Time :</span><span class="field__line"></span><span class="field__suffix">AM/PM</span></div>
      </div>
      <div class="days">
        <span class="day">Mon <span class="day__box"></span></span>
        <span class="day">Tue <span class="day__box"></span></span>
        <span class="day">Wed <span class="day__box"></span></span>
        <span class="day">Thu <span class="day__box"></span></span>
        <span class="day">Fri <span class="day__box"></span></span>
        <span class="day">Sat <span class="day__box"></span></span>
      </div>
      <p class="notice">Please give 24 hours notice if you are unable to keep your appointment or<br>a cancellation fee may be charged.</p>
    </div>
  </section>
</body>
</html>
```